Brochure required

Looking at getting business brochure designed for my solar sales company. i will require a range of products to be listed on the brochure I require a simple/ elegent / professional looking brochure.

I am happy to provide designer with all the required information that must go into the brochure. otherwise please visit www.quillebartow.com.au and view the products which i would like to allocate into the brochure aswell as our company logo and a little about me section

```html
<!DOCTYPE html>
<html lang="en">
<head>
<meta charset="utf-8">
<title>Quillebartow Brochure Cover Spread</title>
<link href="https://fonts.googleapis.com/css2?family=Poppins:wght@400;700;800&family=Roboto:wght@300;400;500&display=swap" rel="stylesheet">
<style>
  :root {
    --bg: #efefef;
    --grey: #dedede;
    --navy: #0c6296;
    --sky: #2d9bcb;
    --green: #0f9a66;
    --teal: #1fb98c;
    --yellow: #e3c52a;
    --ink: #111111;
    --white: #ffffff;
    --photo-top: #cfe6f2;
    --photo-mid: #3f86b8;
    --photo-low: #1f5f96;
  }
  * { margin: 0; padding: 0; box-sizing: border-box; }
  html, body { width: 1200px; height: 840px; overflow: hidden; background: var(--bg); }
  .spread {
    position: absolute; left: 40px; top: 24px;
    width: 1120px; height: 792px;
    display: flex;
    box-shadow: 0 6px 24px rgba(0,0,0,.12);
  }
  .page { position: relative; width: 560px; height: 792px; overflow: hidden; }
  .page svg.art { position: absolute; inset: 0; }
  .brand { position: absolute; font-family: "Poppins", sans-serif; }
  .brand-name {
    display: flex; align-items: center; gap: 8px;
    font-weight: 800; font-size: 30px; line-height: 1; letter-spacing: .5px;
  }
  .brand-mark { width: 20px; height: 20px; }
  .brand-tagline {
    font-family: "Roboto", sans-serif; font-weight: 400;
    font-size: 12.5px; letter-spacing: 2.6px; margin-top: 6px; margin-left: 2px;
  }
  .back .brand { left: 36px; top: 34px; color: var(--ink); }
  .back .brand-mark { background: var(--green); }
  .front .brand { left: 28px; top: 40px; color: var(--white); }
  .front .brand-mark { background: var(--white); }

  .contact {
    position: absolute; left: 70px; top: 540px;
    color: var(--white); font-family: "Roboto", sans-serif;
  }
  .contact-title { font-family: "Poppins", sans-serif; font-size: 19px; font-weight: 400; letter-spacing: 1px; margin-bottom: 14px; }
  .contact-list { list-style: none; font-size: 11.5px; font-weight: 300; }
  .contact-list li { display: flex; align-items: center; gap: 10px; margin-bottom: 9px; }
  .contact-list svg { width: 12px; height: 12px; flex: none; }

  .headline {
    position: absolute; left: 150px; top: 478px; width: 400px;
    color: var(--white); font-family: "Poppins", sans-serif;
  }
  .headline-main { font-weight: 800; font-size: 72px; line-height: .95; letter-spacing: 1px; }
  .headline-sub { font-weight: 400; font-size: 54px; line-height: 1; letter-spacing: 2px; margin-top: 2px; }
  .headline-band {
    position: absolute; left: -14px; top: 128px;
    background: var(--yellow); color: var(--ink);
    font-family: "Roboto", sans-serif; font-weight: 400; font-size: 24px;
    padding: 2px 16px; letter-spacing: .5px; white-space: nowrap;
  }
  .headline-sub, .headline-main { position: relative; z-index: 1; }
  .spine-url {
    position: absolute; left: 40px; top: 706px;
    color: var(--white); font-family: "Roboto", sans-serif; font-size: 11px; font-weight: 300;
    transform: rotate(31deg); transform-origin: left top; letter-spacing: .4px;
  }
</style>
</head>
<body>
<main class="spread">
  <section class="page back">
    <svg class="art" viewBox="0 0 560 792" width="560" height="792" aria-hidden="true">
      <rect width="560" height="792" fill="var(--grey)"/>
      <polygon points="0,300 430,0 560,0 560,640 0,480" fill="var(--navy)"/>
      <polygon points="0,480 560,640 560,792 0,792" fill="var(--green)"/>
    </svg>
    <div class="brand">
      <div class="brand-name"><span class="brand-mark"></span>Quillebartow</div>
      <div class="brand-tagline">Solutions for a changing world</div>
    </div>
    <div class="contact">
      <h2 class="contact-title">CONTACT</h2>
      <ul class="contact-list">
        <li><svg viewBox="0 0 12 12"><path d="M2.5 1 L4.5 1 L5 3.5 L3.8 4.5 Q5 7 7.5 8.2 L8.5 7 L11 7.5 L11 9.5 Q10.5 11 9 11 Q1 10 1 3 Q1 1.5 2.5 1Z" fill="currentColor"/></svg>0400 123 987</li>
        <li><svg viewBox="0 0 12 12"><rect x="1" y="2.5" width="10" height="7" fill="currentColor"/><path d="M1 2.5 L6 6.5 L11 2.5" stroke="var(--green)" fill="none" stroke-width="1"/></svg>info@quillebartow.com</li>
        <li><svg viewBox="0 0 12 12" fill="none" stroke="currentColor" stroke-width="1"><circle cx="6" cy="6" r="5"/><ellipse cx="6" cy="6" rx="2.2" ry="5"/><path d="M1 6 H11 M2 3.5 H10 M2 8.5 H10"/></svg>www.quillebartow.com.au</li>
      </ul>
    </div>
  </section>

  <section class="page front">
    <svg class="art" viewBox="0 0 560 792" width="560" height="792">
      <defs>
        <linearGradient id="photoTone" x1="0" y1="0" x2="0" y2="1">
          <stop offset="0" stop-color="var(--photo-top)"/>
          <stop offset=".3" stop-color="var(--photo-mid)"/>
          <stop offset="1" stop-color="var(--photo-low)"/>
        </linearGradient>
        <linearGradient id="bandTone" x1="0" y1="0" x2="0" y2="1">
          <stop offset="0" stop-color="#38a8d4"/>
          <stop offset="1" stop-color="#1f88bb"/>
        </linearGradient>
      </defs>
      <rect width="560" height="792" fill="var(--sky)"/>
      <polygon points="0,0 240,0 0,600" fill="url(#bandTone)"/>
      <polygon role="img" aria-label="Photo of a technician in a hard hat and hi-vis vest working across a rooftop field of solar panels under a cloudy sky" points="240,0 560,0 560,792 300,792 80,660 0,600" fill="url(#photoTone)"/>
      <polygon points="0,600 80,660 300,792 0,792" fill="var(--teal)"/>
    </svg>
    <div class="brand">
      <div class="brand-name"><span class="brand-mark"></span>Quillebartow</div>
      <div class="brand-tagline">Solutions for a changing world</div>
    </div>
    <div class="headline">
      <h1 class="headline-main">ENERGY</h1>
      <p class="headline-sub">SOLUTIONS</p>
      <p class="headline-band">For A CHANGING WORLD</p>
    </div>
    <p class="spine-url">www.quillebartow.com.au</p>
  </section>
</main>
</body>
</html>
```